TA BRAMLEY BUSINESS CARD DESIGN PROJECT

We need to utilize our logo that was expertly created on PixelHarbor and now need to match this with a business card design.

```html
<!DOCTYPE html>
<html lang="en">
<head>
<meta charset="utf-8">
<title>TA Bramley Business Card</title>
<link href="https://fonts.googleapis.com/css2?family=Montserrat:wght@700;800&family=Open+Sans:wght@400;600&display=swap" rel="stylesheet">
<style>
  :root {
    --brand-blue: #1659a8;
    --ink: #111111;
    --paper: #ffffff;
    --backdrop: #333333;
    --rule: #222222;
  }
  html, body {
    margin: 0;
    padding: 0;
    width: 1200px;
    height: 780px;
    overflow: hidden;
    background: var(--backdrop);
  }
  .canvas {
    position: relative;
    width: 1200px;
    height: 780px;
    display: flex;
    align-items: center;
    justify-content: center;
    gap: 30px;
  }
  .card {
    position: relative;
    width: 560px;
    height: 320px;
    overflow: hidden;
    box-shadow: 0 10px 24px rgba(0,0,0,0.45);
  }

  /* Back side */
  .card-back {
    background: var(--brand-blue);
    display: flex;
    align-items: center;
    justify-content: center;
  }
  .back-wordmark {
    display: flex;
    align-items: center;
    gap: 18px;
  }
  .back-wordmark .mark-dot {
    width: 56px;
    height: 56px;
    border-radius: 50%;
    background: var(--paper);
  }
  .back-wordmark .wordmark-text {
    font-family: "Montserrat", sans-serif;
    font-weight: 800;
    font-size: 50px;
    letter-spacing: 4px;
    color: var(--paper);
  }

  /* Front side */
  .card-front { background: var(--paper); }
  .front-wordmark {
    position: absolute;
    left: 0;
    top: 0;
    width: 330px;
    height: 250px;
    display: flex;
    align-items: center;
    justify-content: center;
    gap: 10px;
  }
  .front-wordmark .mark-dot {
    width: 30px;
    height: 30px;
    border-radius: 50%;
    background: var(--brand-blue);
  }
  .front-wordmark .wordmark-text {
    font-family: "Montserrat", sans-serif;
    font-weight: 800;
    font-size: 30px;
    letter-spacing: 2px;
    color: var(--brand-blue);
  }
  .divider {
    position: absolute;
    left: 330px;
    top: 50px;
    width: 1px;
    height: 180px;
    background: var(--rule);
  }
  .contact-block {
    position: absolute;
    left: 352px;
    top: 62px;
  }
  .person-name {
    margin: 0;
    font-family: "Montserrat", sans-serif;
    font-weight: 800;
    font-size: 24px;
    color: var(--brand-blue);
    line-height: 1.1;
    white-space: nowrap;
  }
  .person-title {
    margin: 4px 0 18px;
    font-family: "Open Sans", sans-serif;
    font-weight: 600;
    font-size: 13px;
    color: var(--ink);
  }
  .contact-list {
    list-style: none;
    margin: 0;
    padding: 0;
    font-family: "Open Sans", sans-serif;
    font-size: 13px;
    color: var(--ink);
  }
  .contact-list li {
    display: flex;
    align-items: center;
    gap: 8px;
    line-height: 22px;
  }
  .contact-list svg { width: 12px; height: 12px; flex: none; }
  .address-band {
    position: absolute;
    left: 0;
    bottom: 28px;
    width: 100%;
    height: 32px;
    background: var(--brand-blue);
    display: flex;
    align-items: center;
  }
  .address-text {
    padding-left: 24px;
    font-family: "Open Sans", sans-serif;
    font-size: 13px;
    color: var(--paper);
    letter-spacing: 0.3px;
  }
  .band-accent {
    position: absolute;
    right: 0;
    bottom: 60px;
    width: 70px;
    height: 24px;
  }
  .band-wordmark {
    position: absolute;
    right: 74px;
    bottom: 36px;
    font-family: "Montserrat", sans-serif;
    font-weight: 800;
    font-size: 13px;
    letter-spacing: 1px;
    color: var(--paper);
  }
</style>
</head>
<body>
<main class="canvas">
  <section class="card card-back" aria-label="Business card back">
    <div class="back-wordmark">
      <span class="mark-dot"></span>
      <span class="wordmark-text">TA BRAMLEY</span>
    </div>
  </section>

  <section class="card card-front" aria-label="Business card front">
    <div class="front-wordmark">
      <span class="mark-dot"></span>
      <span class="wordmark-text">TA BRAMLEY</span>
    </div>
    <div class="divider"></div>
    <div class="contact-block">
      <h1 class="person-name">Mira Kovalenko</h1>
      <p class="person-title">Managing Director</p>
      <ul class="contact-list">
        <li>
          <svg viewBox="0 0 24 24" aria-hidden="true"><path fill="var(--brand-blue)" d="M6.6 10.8a15.1 15.1 0 0 0 6.6 6.6l2.2-2.2a1 1 0 0 1 1-.25 11.4 11.4 0 0 0 3.6.57 1 1 0 0 1 1 1V20a1 1 0 0 1-1 1A17 17 0 0 1 3 4a1 1 0 0 1 1-1h3.5a1 1 0 0 1 1 1c0 1.25.2 2.45.57 3.57a1 1 0 0 1-.25 1z"/></svg>
          (555) 240-1187
        </li>
        <li>
          <svg viewBox="0 0 24 24" aria-hidden="true"><rect x="2" y="5" width="20" height="14" rx="1" fill="var(--brand-blue)"/><path d="M3 6l9 7 9-7" fill="none" stroke="#fff" stroke-width="2"/></svg>
          hello@tabramley.com
        </li>
        <li>
          <svg viewBox="0 0 24 24" aria-hidden="true"><circle cx="12" cy="12" r="10" fill="var(--brand-blue)"/><path d="M2 12h20M12 2c3 3 3 17 0 20M12 2c-3 3-3 17 0 20" fill="none" stroke="#fff" stroke-width="1.5"/></svg>
          www.tabramley.com
        </li>
      </ul>
    </div>
    <svg class="band-accent" viewBox="0 0 70 24" aria-hidden="true"><polygon points="14,0 70,0 70,24 0,24" fill="var(--ink)"/></svg>
    <span class="band-wordmark">TA BRAMLEY</span>
    <div class="address-band">
      <span class="address-text">418 Lakeshore Ave. Suite 120 Riverton, TX 75010</span>
    </div>
  </section>
</main>
</body>
</html>
```